we can communicate on this, but i want to follow the approach we took on Pellew|Marsh & Quinlan but i feel the card front needs the black background and the platinum and gold logo. The back? I am open. we can use the same info from PM&Q. Velmont Arc is an enhanced equity investment fund - basically a very exclusive boutique hedge fund that uses only stock options. very advanced things. hope you are interested

Contact Information for Business Card

Dr. Lewis T. Brennick, CFA
Scientifique de fusée financière
701.555.0143
LTBquant47@mailvantor.com

4718 Willow Creek Bend W.
West Fargo, ND 58078

No web site

Colors

Designer to choose colors to be used in the design.

Requirements
Nice to have
• I tend to prefer the most visible applications of the logo to include logo and name, the logo version with a black background and the gold and platinum components separated by the black. I see this working well for a single side (logo and name - this is card front to me).
• I am fairly open to other treatments on the reverse side with the data. To me, it makes sense to have a different color rendition of the logo on the reverse and it may be a muted black tone on tone or an oversized portion that would have spot UV. Or, the reverse may play with colors and layout
Should not have
• Other colors = no no
• Decorative font

```html
<!DOCTYPE html>
<html lang="en">
<head>
<meta charset="utf-8">
<title>Velmont Arc – Business Card</title>
<link rel="stylesheet" href="https://fonts.googleapis.com/css2?family=Cinzel:wght@400;600&display=swap">
<style>
  :root {
    --backdrop: #2e2e2e;
    --card-black: #1c1c1c;
    --tone-on-tone: #262626;
    --tone-mark: #2f2f2f;
    --gold: #c9a233;
    --platinum: #e9e7ea;
    --text-light: #f2f2f2;
  }
  * { box-sizing: border-box; margin: 0; padding: 0; }
  html, body {
    width: 1200px; height: 900px; overflow: hidden;
    background: var(--backdrop);
    font-family: "Cinzel", serif;
  }
  .canvas {
    position: relative; width: 1200px; height: 900px;
  }
  .card {
    position: absolute; left: 250px;
    width: 700px; height: 400px;
    background: var(--card-black);
    border-radius: 28px;
    overflow: hidden;
  }
  .card--back { top: 40px; }
  .card--front { top: 465px; }

  /* Back: tone-on-tone brand */
  .back-brand {
    position: absolute; left: 0; right: 0; top: 110px;
    display: flex; flex-direction: column; align-items: center; gap: 18px;
  }
  .back-brand__dot {
    width: 120px; height: 120px; border-radius: 50%;
    background: var(--tone-mark);
  }
  .back-brand__name {
    font-weight: 600; font-size: 46px; letter-spacing: 4px;
    color: var(--tone-mark); text-transform: uppercase;
  }

  /* Front: brand + contact */
  .front-brand {
    position: absolute; left: 40px; top: 95px; width: 300px;
    display: flex; flex-direction: column; align-items: center; gap: 22px;
  }
  .front-brand__dot {
    width: 110px; height: 110px; border-radius: 50%;
    background: var(--gold);
  }
  .front-brand__name {
    font-weight: 600; font-size: 38px; letter-spacing: 3px;
    color: var(--text-light); text-transform: uppercase; white-space: nowrap;
  }
  .divider {
    position: absolute; left: 360px; top: 80px;
    width: 1.5px; height: 240px; background: var(--gold);
  }
  .contact {
    position: absolute; left: 385px; top: 82px; right: 20px;
    color: var(--text-light); text-transform: uppercase;
    font-size: 15px; line-height: 1.45;
  }
  .contact__name {
    color: var(--gold); font-weight: 600; font-size: 21px; line-height: 1.2;
  }
  .contact__credential { margin-bottom: 6px; }
  .contact__title { margin-bottom: 10px; }
  .contact__address { margin-bottom: 10px; }
  .contact__line { display: flex; align-items: center; gap: 10px; }
  .contact__line svg { width: 16px; height: 16px; flex: none; }
</style>
</head>
<body>
<main class="canvas">
  <section class="card card--back" aria-label="Card back">
    <div class="back-brand">
      <div class="back-brand__dot"></div>
      <div class="back-brand__name">Velmont Arc</div>
    </div>
  </section>

  <section class="card card--front" aria-label="Card front">
    <div class="front-brand">
      <div class="front-brand__dot"></div>
      <div class="front-brand__name">Velmont Arc</div>
    </div>
    <div class="divider"></div>
    <div class="contact">
      <p class="contact__name">Dr. Lewis T. Brennick</p>
      <p class="contact__credential">CFA</p>
      <p class="contact__title">Scientifique de fusée financière</p>
      <p class="contact__address">4718 Willow Creek Bend W.<br>West Fargo, ND 58078</p>
      <p class="contact__line">
        <svg viewBox="0 0 24 24" aria-hidden="true"><path fill="#c9a233" d="M6.6 10.8a15.1 15.1 0 0 0 6.6 6.6l2.2-2.2a1 1 0 0 1 1-.25 11.4 11.4 0 0 0 3.6.57 1 1 0 0 1 1 1V20a1 1 0 0 1-1 1A17 17 0 0 1 3 4a1 1 0 0 1 1-1h3.5a1 1 0 0 1 1 1c0 1.25.2 2.45.57 3.57a1 1 0 0 1-.25 1z"/></svg>
        701.555.0143
      </p>
      <p class="contact__line">
        <svg viewBox="0 0 24 24" aria-hidden="true"><rect x="2" y="5" width="20" height="14" rx="1.5" fill="#c9a233"/><path d="M3 6l9 7 9-7" fill="none" stroke="#1c1c1c" stroke-width="1.8"/></svg>
        LTBquant47@mailvantor.com
      </p>
    </div>
  </section>
</main>
</body>
</html>
```